Business card for a Exhibition booth fabrication company

Hi. My company would like to change our corporate name card. We are an events and Exhibition stand builder company. We would like our corporate name card to resonate what we do. I need someone to create something unique that relates to the industry that I am in. The graphic designer should be creative to incorporate the elements of my industry and try to blend in well in the design of the card. Our aim is to ensure that we are unique and our card can look different from our competitors.
Updates

Target Market(s)

Marketing and events manager from all companies

Contact Information for Business Card

The business card should have the following details:
Name
Job Title
Email
Website

Colors

Designer to choose colors to be used in the design.

Requirements
Must have
• The card must be look something that is relevant to the service that I am providing. My website is: www.velmora-buildworks.com
• You can see my website to get more information on what service that I am doing
Nice to have
• On the back of my card, I would like to have a globe image with the incorporation of my company logo. This is to indicate that my services can be done in any part of the world.

```html
<!DOCTYPE html>
<html lang="en">
<head>
<meta charset="utf-8">
<title>Velmora Buildworks – Business Card</title>
<link href="https://fonts.googleapis.com/css2?family=Open+Sans:wght@400;600;700&display=swap" rel="stylesheet">
<style>
  :root {
    --brand-red: #e3202c;
    --ink-grey: #4a4a4a;
    --soft-grey: #6b6b6b;
    --rule-grey: #d6d6d6;
    --card-white: #ffffff;
    --backdrop: #e9e6e2;
    --globe-light: #f1f1f1;
    --globe-mid: #dedede;
  }
  html, body {
    margin: 0;
    width: 1200px;
    height: 997px;
    overflow: hidden;
    background: var(--backdrop);
    font-family: "Open Sans", Arial, sans-serif;
  }
  .sheet { position: relative; width: 1200px; height: 997px; }
  .card {
    position: absolute;
    left: 320px;
    width: 560px;
    height: 320px;
    background: var(--card-white);
    box-shadow: 0 6px 18px rgba(0,0,0,0.12);
    overflow: hidden;
  }
  .card--front { top: 120px; }
  .card--back { top: 520px; }

  .brand {
    position: absolute;
    text-align: center;
    white-space: nowrap;
  }
  .brand__dot {
    display: block;
    width: 46px;
    height: 46px;
    margin: 0 auto 12px;
    border-radius: 50%;
    background: var(--brand-red);
  }
  .brand__name {
    font-weight: 700;
    font-size: 14px;
    letter-spacing: 2px;
    color: var(--ink-grey);
    text-transform: uppercase;
  }

  /* Front */
  .brand--front { left: 20px; top: 110px; width: 240px; }
  .divider {
    position: absolute;
    left: 272px;
    top: 48px;
    width: 1px;
    height: 150px;
    background: var(--rule-grey);
  }
  .contact {
    position: absolute;
    left: 292px;
    top: 48px;
    font-size: 12.5px;
    line-height: 1.45;
    color: var(--soft-grey);
  }
  .contact__name {
    margin: 0;
    font-size: 14px;
    font-weight: 700;
    color: var(--brand-red);
    text-transform: uppercase;
  }
  .contact__title { margin: 0 0 4px; }
  .contact__row { display: flex; align-items: center; gap: 6px; }
  .contact__row svg { flex: none; }
  .contact__address { margin-top: 6px; }
  .web-band {
    position: absolute;
    right: 0;
    top: 228px;
    width: 290px;
    height: 24px;
    padding-left: 12px;
    box-sizing: border-box;
    background: var(--brand-red);
    clip-path: polygon(8px 0, 100% 0, 100% 100%, 0 100%);
    color: var(--card-white);
    font-size: 12px;
    letter-spacing: 0.8px;
    display: flex;
    align-items: center;
    justify-content: center;
  }

  /* Back */
  .globe-map {
    position: absolute;
    left: 130px;
    top: 40px;
    width: 440px;
    height: 440px;
    border-radius: 50%;
    background: radial-gradient(circle at 40% 35%, var(--globe-light) 0%, var(--globe-mid) 55%, rgba(222,222,222,0.35) 70%, rgba(255,255,255,0) 71%);
  }
  .brand--back { left: 140px; top: 92px; width: 280px; }
  .brand--back .brand__dot { width: 54px; height: 54px; }
  .brand--back .brand__name { font-size: 17px; letter-spacing: 2.5px; }
</style>
</head>
<body>
<main class="sheet">
  <section class="card card--front" aria-label="Business card front">
    <div class="brand brand--front">
      <span class="brand__dot"></span>
      <span class="brand__name">Velmora Buildworks</span>
    </div>
    <div class="divider"></div>
    <div class="contact">
      <p class="contact__name">Daniel Reyes</p>
      <p class="contact__title">President</p>
      <div class="contact__row">
        <svg width="10" height="10" viewBox="0 0 10 10" aria-hidden="true"><path d="M2 1 L4 3 L3 4 Q4 6 6 7 L7 6 L9 8 L8 9 Q3 9 1 2 Z" fill="var(--brand-red)"/></svg>
        <span>+974 5550 1234</span>
      </div>
      <div class="contact__row">
        <svg width="10" height="8" viewBox="0 0 10 8" aria-hidden="true"><rect width="10" height="8" rx="1" fill="var(--brand-red)"/><path d="M0.5 0.8 L5 4.5 L9.5 0.8" stroke="#fff" stroke-width="1" fill="none"/></svg>
        <span>info@velmora-buildworks.com</span>
      </div>
      <div class="contact__address">P.O. Box 4120,<br>Marina Lane, Doha - Qatar</div>
    </div>
    <div class="web-band">www.velmora-buildworks.com</div>
  </section>

  <section class="card card--back" aria-label="Business card back">
    <div class="globe-map" role="img" aria-label="Faint grey world map wrapped on a globe, showing worldwide service"></div>
    <div class="brand brand--back">
      <span class="brand__dot"></span>
      <span class="brand__name">Velmora Buildworks</span>
    </div>
  </section>
</main>
</body>
</html>
```